Venture 482 - Lumora Book Cover

I am looking for a Lumora book cover for my book about "Venture 482".
The Book is Titled:
Venture 482 Ascended
Shaping Outcomes: Paths To Unlocking Cosmic Truths
Author is Dorian Pell
Here is a book description that may help you understand more about it:
Inspired by the genius of Edwin Marlowe, this comprehensive guide delves into the ancient wisdom and cutting-edge science behind the 482 method, a powerful tool for manifesting your desires. Whether you're seeking personal growth, financial success, or spiritual enlightenment, this book provides advanced techniques and methods to transform your dreams into reality.
Any questions please ask.
Thanks
Owen

```html
<!DOCTYPE html>
<html lang="en">
<head>
<meta charset="utf-8">
<title>Venture 482 Ascended — Dorian Pell</title>
<link href="https://fonts.googleapis.com/css2?family=Marcellus&family=Tinos:wght@400;700&display=swap" rel="stylesheet">
<style>
  :root {
    --sky-top: #332a5e;
    --sky-mid: #261c4c;
    --sky-low: #140b28;
    --sky-haze: rgba(150, 140, 210, 0.28);
    --title-ink: #f8e9df;
    --band-fill: #fcf8df;
    --band-ink: #3b2c60;
    --subtitle-ink: #ffffff;
  }
  html, body {
    margin: 0;
    padding: 0;
    overflow: hidden;
    background: var(--sky-low);
  }
  .cover {
    position: relative;
    width: 805px;
    height: 1200px;
    overflow: hidden;
    font-family: "Marcellus", serif;
  }
  .cover__sky {
    position: absolute;
    inset: 0;
    background:
      linear-gradient(160deg, var(--sky-haze) 0%, transparent 40%),
      linear-gradient(180deg, var(--sky-top) 0%, var(--sky-mid) 50%, var(--sky-low) 100%);
  }
  .title-block {
    margin: 0;
    font-weight: 400;
  }
  .title {
    position: absolute;
    left: 0;
    width: 100%;
    text-align: center;
    color: var(--title-ink);
    display: block;
  }
  .title__word {
    top: 305px;
    font-size: 118px;
    line-height: 1;
    letter-spacing: 1px;
  }
  .title__number {
    top: 424px;
    font-size: 244px;
    line-height: 1;
    left: 4px;
  }
  .title__band {
    position: absolute;
    left: 170px;
    top: 638px;
    width: 464px;
    height: 57px;
    background: var(--band-fill);
    color: var(--band-ink);
    font-size: 38px;
    line-height: 57px;
    text-align: center;
    letter-spacing: 29px;
    text-indent: 29px;
  }
  .subtitle {
    position: absolute;
    left: 0;
    width: 786px;
    top: 956px;
    text-align: center;
    color: var(--subtitle-ink);
    font-family: "Tinos", serif;
    font-size: 29px;
    line-height: 37px;
    margin: 0;
  }
  .subtitle__lead {
    display: block;
    font-weight: 700;
    text-transform: uppercase;
    letter-spacing: -0.3px;
  }
  .author {
    position: absolute;
    left: 0;
    width: 786px;
    top: 1106px;
    text-align: center;
    color: var(--title-ink);
    font-size: 49px;
    line-height: 1.2;
    letter-spacing: 20px;
    text-indent: 20px;
    margin: 0;
    font-weight: 400;
  }
</style>
</head>
<body>
<main class="cover">
  <div class="cover__sky" role="img" aria-label="Starry violet night sky with the Milky Way and a faint constellation"></div>

  <h1 class="title-block">
    <span class="title title__word">VENTURE</span>
    <span class="title title__number">482</span>
    <span class="title__band">ASCENDED</span>
  </h1>

  <p class="subtitle">
    <span class="subtitle__lead">Shaping Outcomes:</span>
    Paths to unlocking<br>cosmic truths
  </p>

  <p class="author">DORIAN PELL</p>
</main>
</body>
</html>
```